Dynamic Business Card for Sports Supplements Company

Hi! I'm looking for an awesome business card to match my existing sports supplement company. I have uploaded my current company logo and screenshot of the front page of my website.

I would like to have something dynamic and interesting and utilize the colors in the website - the reds and purples

The business card should be double sided and focus on a unique eye-catching design on the back and include all the relevant company info.

Most importantly, it should say somewhere: "Sign up on our website for a coupon code."

Target Market(s)

Mostly for women gym goers but it shouldn't be too feminine. It should be in keeping with the website design. It should flow and clearly be connected to it

Industry/Entity Type

Business

Contact Information for Business Card

Lorraine K. Vestal
CEO
LVestal@Quorvanexco.com
www.quorvanexco.com
555.417.3820
P.O. Box 47315
Dalmoor, Westlane 00000

Sign up on our website for a coupon code

Font styles to use
Serif
Sans Serif
Other font styles liked:
• Novecento font family and "Quorvanex" is in AR Destine font

Requirements
Must have
• One side should be a bold Quorvanex logo design. Even just the symbol itself may be o.k. (see attached file)

```html
<!DOCTYPE html>
<html lang="en">
<head>
<meta charset="utf-8">
<title>Quorvanex Business Card</title>
<link rel="stylesheet" href="https://fonts.googleapis.com/css2?family=Saira:wght@500;700&family=Open+Sans:wght@400;600&display=swap">
<style>
  :root {
    --canvas: #d6d6d6;
    --red: #e41f26;
    --ink: #1a1a1a;
    --band: #141414;
    --white: #ffffff;
    --back-top: #2b2c2f;
    --back-bottom: #0f0f11;
    --muted: #cfcfcf;
  }
  * { margin: 0; padding: 0; box-sizing: border-box; }
  html, body { width: 1200px; height: 900px; overflow: hidden; }
  body {
    background: var(--canvas);
    position: relative;
    font-family: "Open Sans", Arial, sans-serif;
  }
  .card {
    position: absolute;
    top: 271px;
    width: 457px;
    height: 282px;
    border-radius: 14px;
    overflow: hidden;
  }
  .card-front { left: 137px; background: var(--white); }
  .card-back {
    left: 627px;
    background: radial-gradient(ellipse at 55% 30%, var(--back-top), var(--back-bottom) 80%);
  }

  .brand-name {
    font-family: "Saira", Arial, sans-serif;
    font-weight: 700;
    line-height: 1;
    white-space: nowrap;
  }
  .brand-tagline {
    font-family: "Saira", Arial, sans-serif;
    font-weight: 500;
    text-transform: uppercase;
    line-height: 1;
    white-space: nowrap;
  }

  .front-brand { position: absolute; left: 27px; top: 25px; }
  .front-brand .brand-name { color: var(--red); font-size: 35px; letter-spacing: 4.2px; }
  .front-brand .brand-tagline { color: var(--ink); font-size: 11px; letter-spacing: 3px; margin-top: 1px; }

  .address {
    position: absolute;
    right: 28px;
    top: 23px;
    text-align: right;
    font-size: 12.5px;
    line-height: 17px;
    color: var(--ink);
    font-style: normal;
  }

  .contact-band {
    position: absolute;
    left: 0;
    top: 124px;
    width: 287px;
    height: 129px;
    background: var(--band);
    padding: 10px 0 0 27px;
    color: var(--white);
  }
  .person-name {
    font-family: "Saira", Arial, sans-serif;
    font-weight: 500;
    font-size: 15.5px;
    letter-spacing: 1.2px;
    text-transform: uppercase;
    color: var(--red);
    line-height: 20px;
  }
  .person-role { font-size: 13px; line-height: 18px; font-weight: 600; }
  .contact-list { list-style: none; margin-top: 14px; }
  .contact-list li {
    display: flex;
    align-items: center;
    gap: 8px;
    font-size: 12.5px;
    line-height: 20.5px;
  }
  .contact-list svg { width: 11px; height: 11px; fill: var(--red); flex: none; }

  .brand-square {
    position: absolute;
    left: 305px;
    top: 126px;
    width: 124px;
    height: 124px;
    background: var(--red);
  }

  .back-content {
    position: absolute;
    inset: 0;
    display: flex;
    flex-direction: column;
    align-items: center;
    padding-top: 82px;
  }
  .back-square { width: 46px; height: 46px; background: var(--red); }
  .back-content .brand-name { color: var(--white); font-size: 30px; letter-spacing: 2px; margin-top: 36px; }
  .back-content .brand-tagline { color: var(--muted); font-size: 9.5px; letter-spacing: 2.2px; margin-top: 2px; }
  .coupon {
    margin-top: 24px;
    font-size: 12.5px;
    color: var(--white);
  }
  .coupon .highlight { color: var(--red); }
</style>
</head>
<body>

<section class="card card-front" aria-label="Business card front">
  <div class="front-brand">
    <div class="brand-name">QUORVANEX</div>
    <div class="brand-tagline">Your Strength Companion</div>
  </div>

  <address class="address">
    P.O. Box 47315<br>Dalmoor,<br>Westlane 00000
  </address>

  <div class="contact-band">
    <div class="person-name">Lorraine K. Vestal</div>
    <div class="person-role">CEO</div>
    <ul class="contact-list">
      <li>
        <svg viewBox="0 0 12 12" aria-hidden="true"><path d="M1 4c0-2 2-3 5-3s5 1 5 3v1H8.5V3.8h-5V5H1zM2.5 6h7l1 5h-9z"/></svg>
        555.417.3820
      </li>
      <li>
        <svg viewBox="0 0 12 12" aria-hidden="true"><path d="M0 2h12v1.2L6 7 0 3.2zM0 4.6l6 3.8 6-3.8V10H0z"/></svg>
        LVestal@Quorvanexco.com
      </li>
      <li>
        <svg viewBox="0 0 12 12" aria-hidden="true"><circle cx="6" cy="6" r="5.5"/></svg>
        www.quorvanexco.com
      </li>
    </ul>
  </div>

  <div class="brand-square" aria-hidden="true"></div>
</section>

<section class="card card-back" aria-label="Business card back">
  <div class="back-content">
    <div class="back-square" aria-hidden="true"></div>
    <div class="brand-name">QUORVANEX</div>
    <div class="brand-tagline">Your Strength Companion</div>
    <p class="coupon"><span class="highlight">Sign up</span> on our website for a coupon code</p>
  </div>
</section>

</body>
</html>
```